Business Card Design For Office Furniture Clearance Company

Kestrel Office Clearance - our company name pretty much explains what we do, we clear offices for high end clients, mainly plc's and large international companies.

We require a nice looking business card that displays professionalism but without being too serious.

It would be nice to see just a little more than a conventional boring business card, make sure you add some flare.

Industry/Entity Type

Office Furniture

Contact Information for Business Card

CARD 1

Mark Holloway
Director
mark@kestrelofficeclearance.co.uk
m: 07700 153928

t: 01632 960418
www.kestrelofficeclearance.co.uk

Kestrel Office Clearance
Unit K4 B
2-8 Fenwick Lane
Ashworth
Northfield Vale
ZZ9 4QT

free office clearances… you cant get better than that.

CARD 2

Peter Radford
Director
peter@kestrelofficeclearance.co.uk
m: 07700 382615

t: 01632 960418

Kestrel Office Clearance
Unit K4 B
2-8 Fenwick Lane
Ashworth
Northfield Vale
ZZ9 4QT

Font styles to use
Sans Serif

Requirements
Must have
• A white background - as we have a blue logo.
Nice to have
• Nice use of the logo - play around with this and dissect it.

```html
<!DOCTYPE html>
<html lang="en">
<head>
<meta charset="utf-8">
<title>Kestrel Office Clearance – Business Card</title>
<link href="https://fonts.googleapis.com/css2?family=Lato:wght@400;700;900&display=swap" rel="stylesheet">
<style>
  :root {
    --brand-blue: #0a78bf;
    --ink: #2b2b2b;
    --paper: #ffffff;
    --backdrop: #7a7878;
  }
  * { box-sizing: border-box; margin: 0; padding: 0; }
  html, body { width: 1200px; height: 900px; overflow: hidden; }
  body {
    background: var(--backdrop);
    font-family: "Lato", sans-serif;
    position: relative;
  }
  .card {
    position: absolute;
    left: 250px;
    width: 700px;
    height: 400px;
    border-radius: 16px;
    overflow: hidden;
    box-shadow: 0 6px 18px rgba(0,0,0,0.25);
  }
  .card-back { top: 33px; background: var(--brand-blue); }
  .card-front { top: 467px; background: var(--paper); }

  .back-name {
    position: absolute;
    left: 0; right: 0; top: 150px;
    text-align: center;
    color: var(--paper);
    font-weight: 900;
    font-size: 36px;
    line-height: 1.15;
  }
  .back-web {
    position: absolute;
    left: 0; right: 0; bottom: 40px;
    text-align: center;
    color: var(--paper);
    font-size: 14px;
  }

  .front-art { position: absolute; inset: 0; }
  .circle-name {
    position: absolute;
    left: 340px; top: 120px;
    width: 260px;
    text-align: center;
    color: var(--paper);
    font-weight: 900;
    font-size: 30px;
    line-height: 1.15;
  }
  .company {
    position: absolute;
    left: 36px; top: 78px;
    color: var(--brand-blue);
    font-weight: 900;
    font-size: 26px;
    white-space: nowrap;
  }
  .person { position: absolute; left: 60px; top: 158px; }
  .person-name { color: var(--brand-blue); font-weight: 700; font-size: 24px; line-height: 1.1; }
  .person-role { color: var(--ink); font-size: 14px; margin-left: 12px; }
  .address {
    position: absolute; left: 88px; top: 228px;
    color: var(--ink); font-size: 14px; line-height: 1.3; font-style: normal;
  }
  .contacts {
    position: absolute; left: 88px; top: 292px;
    list-style: none; color: var(--ink); font-size: 14px; line-height: 1.3;
  }
  .contacts li { display: flex; align-items: center; gap: 8px; }
  .contacts svg { width: 13px; height: 13px; fill: var(--brand-blue); flex: none; }
  .contacts .icon-web { fill: none; stroke: var(--brand-blue); stroke-width: 1.4; }
</style>
</head>
<body>

<section class="card card-back">
  <div class="back-name">Kestrel<br>Office Clearance</div>
  <div class="back-web">www.kestrelofficeclearance.co.uk</div>
</section>

<section class="card card-front">
  <svg class="front-art" viewBox="0 0 700 400" aria-hidden="true">
    <rect x="518" y="0" width="182" height="400" fill="var(--brand-blue)"/>
    <circle cx="470" cy="185" r="150" fill="var(--brand-blue)"/>
    <circle cx="482" cy="180" r="162" fill="none" stroke="var(--paper)" stroke-width="3"/>
  </svg>
  <div class="circle-name">Kestrel<br>Office<br>Clearance</div>

  <h1 class="company">Kestrel Office Clearance</h1>

  <div class="person">
    <div class="person-name">Mark Holloway</div>
    <div class="person-role">Director</div>
  </div>

  <address class="address">
    Unit K4 B, 2-8 Fenwick Lane<br>
    Ashworth, Northfield Vale<br>
    ZZ9 4QT
  </address>

  <ul class="contacts">
    <li><svg viewBox="0 0 16 16"><path d="M4 1h8a1 1 0 0 1 1 1v12a1 1 0 0 1-1 1H4a1 1 0 0 1-1-1V2a1 1 0 0 1 1-1zm1 2v9h6V3z"/></svg>07700 153928</li>
    <li><svg viewBox="0 0 16 16"><path d="M3 1l3 3-1.5 2a9 9 0 0 0 5.5 5.5L12 10l3 3-2 2C6 15 1 10 1 3z"/></svg>01632 960418</li>
    <li><svg viewBox="0 0 16 16"><path d="M1 3h14v10H1zm1.5 1.5L8 9l5.5-4.5z"/></svg>mark@kestrelofficeclearance.co.uk</li>
    <li><svg class="icon-web" viewBox="0 0 16 16"><circle cx="8" cy="8" r="6.3"/><ellipse cx="8" cy="8" rx="2.8" ry="6.3"/><path d="M1.7 8h12.6"/></svg>www.kestrelofficeclearance.co.uk</li>
  </ul>
</section>

</body>
</html>
```